Sophisticated, clean website reflecting my feminine, playful side to sell my abstract art,

I need a website no more than 3 pages to showcase my paintings, a little about me and some contact info. I do abstracts so looking for something a little edgy, yet feminine and current.
Updates

Hi there, These are some artists websites that I Iike: Marnelvoss.com (I like how airy it is) peterwallombry.com garethpolvens.com (I like how it scrolls) I'll need a place for a photo ( a headshot-i do not have it yet so I'll need to be able to upload that later) as well as an area for my bio. Also, it's important that I will be able to upload any new photos and descriptions easily so it should be user friendly. Lastly, I like in a sunny place so would like to have this seem upbeat and playful as that is how i like to paint. thanks-I'm trying to upload my photos now -

Target Market(s)

ppl ages 35-70 who want large scale art for their homes

Industry/Entity Type

art

Coding

Coded - Design and coding required

Number of Pages Required

3 page

Colors

Designer to choose colors to be used in the design.

Requirements
Must have
• photos of my art, a place for my bio, be easy to reach me. tasteful-nothing too "in your face" -my clients are pretty high end and organized. They like clean lines
Nice to have
• sophisticated background, muted tones in the back-similar clean font throughout-no cursive
Should not have
• too many dark areas. Too many blocks of color. Too serious.

```html
<!DOCTYPE html>
<html lang="en">
<head>
<meta charset="utf-8">
<title>Colette Marwick Art</title>
<link href="https://fonts.googleapis.com/css2?family=Limelight&family=Lato:wght@400;700&display=swap" rel="stylesheet">
<style>
:root{
  --ink:#120604;
  --paper:#ffffff;
  --blush:#f5ece9;
  --stone:#f1f1f1;
  --faint:#ebdcd8;
  --sand:#efe3dc;
  --rust:#9a3a22;
  --text:#2a2220;
  --white:#ffffff;
}
*{margin:0;padding:0;box-sizing:border-box}
html,body{width:1200px;height:3429px;overflow:hidden;background:var(--paper)}
body{position:relative;font-family:"Lato",sans-serif;color:var(--text)}
.display{font-family:"Limelight",serif;color:var(--ink)}
.abs{position:absolute}

/* Header */
.hero{position:absolute;left:0;top:0;width:1200px;height:725px}
.site-logo{left:112px;top:22px;font-size:32px}
.main-nav{left:0;top:28px;width:1200px;font-size:20px;color:var(--ink)}
.main-nav a{position:absolute;color:var(--ink);text-decoration:none}
.hero-title{left:0;width:1200px;text-align:center}
.hero-kicker{top:168px;font-size:36px}
.hero-name{top:218px;font-size:44px}
.rule{position:absolute;height:2px;background:var(--ink)}

/* About */
.about-frame{left:65px;top:740px;width:365px;height:443px;background:var(--stone);border-radius:150px 150px 60px 60px}
.about-photo{left:112px;top:793px;width:318px;height:385px;border-radius:120px 0 0 0;background:linear-gradient(160deg,#f3f1ee 0%,#e6e0da 45%,#b8a79b 70%,#6c8299 100%)}
.about-pill{left:443px;top:891px;width:130px;height:156px;background:var(--stone);border-radius:65px 65px 0 0}
.about-oval{left:443px;top:1060px;width:130px;height:161px;border-radius:50%;background:radial-gradient(circle at 45% 50%,#e9e4dc 0%,#2f8a86 40%,#1e4d5a 70%,#8a4a2a 100%)}
.section-title{font-size:40px}
.about-title{left:608px;top:808px}
.about-text{left:608px;top:913px;width:480px;font-size:17px;line-height:28px;text-align:justify}
.about-text p+p{margin-top:8px}
.more-link{left:608px;top:1138px;width:31px;height:31px}

/* Paintings */
.paintings{left:0;top:1238px;width:1200px;height:1820px;background:var(--blush)}
.paintings-title{left:0;width:1200px;top:1358px;text-align:center}
.art{position:absolute;box-shadow:0 2px 6px rgba(0,0,0,.12)}
.art-circles{left:112px;top:1486px;width:528px;height:645px;border-radius:264px 264px 0 0;background:linear-gradient(150deg,#eef1f2 0%,#d8a13b 25%,#eaf0f3 45%,#3a6fb0 60%,#eef0ef 75%,#d4702c 100%)}
.art-drips{left:674px;top:1704px;width:414px;height:424px;background:linear-gradient(180deg,#e6e2dc 0%,#ddd8d1 38%,#5ba6cf 44%,#a9cfe2 70%,#e8ebec 100%)}
.art-teal{left:116px;top:2157px;width:411px;height:423px;background:linear-gradient(180deg,#e9e0d2 0%,#e4d9c8 22%,#157f74 24%,#0f6a63 74%,#e6dccb 76%,#ded3c2 100%)}
.art-burst{left:560px;top:2155px;width:528px;height:678px;border-radius:0 0 264px 264px;background:radial-gradient(circle at 50% 60%,#1e1a1a 0%,#7a4a2c 22%,#2f9a62 48%,#dfe6e0 70%,#56b46a 100%)}
.ghost{font-family:"Limelight",serif;color:var(--faint);font-size:92px;line-height:1}
.ghost-one{left:676px;top:1568px}
.ghost-two{left:112px;top:2628px}

/* Footer */
.footer-band{left:0;top:2946px;width:1200px;height:483px}
.footer{color:var(--white);font-size:16px}
.footer .display{color:var(--white)}
.col-title{font-size:20px;top:3056px}
.contact-item{left:148px;line-height:30px}
.icon{left:110px;width:22px;height:22px}
.quick-links{left:419px;top:3099px;line-height:30px}
.field{position:absolute;border:1.5px solid var(--white);border-radius:8px;color:var(--white);font-size:17px;padding:13px 25px}
.send{left:641px;top:3270px;width:120px;height:48px;background:var(--sand);border-radius:8px;color:var(--ink);font-weight:700;font-size:17px;text-align:center;line-height:48px}
.follow{left:109px;top:3283px;font-size:20px}
.social-ring{left:196px;top:3279px;width:41px;height:41px;border:1.5px solid var(--white);border-radius:50%}
.footer-rule{left:112px;top:3362px;width:976px;height:1px;background:rgba(255,255,255,.35)}
.copyright{left:0;width:1200px;top:3382px;text-align:center;font-size:17px}
</style>
</head>
<body>

<svg class="hero" viewBox="0 0 1200 725" role="img" aria-label="Close-up of an abstract painting with loose rust and dark red brushstrokes on raw canvas">
  <defs>
    <linearGradient id="heroPaint" x1="0" y1="0" x2="1" y2="1">
      <stop offset="0" stop-color="#f1e6dd"/>
      <stop offset=".35" stop-color="#eadcd2"/>
      <stop offset=".6" stop-color="#c9866a"/>
      <stop offset=".85" stop-color="#e8d9cf"/>
      <stop offset="1" stop-color="#b5694b"/>
    </linearGradient>
  </defs>
  <path d="M0 0H1200V612Q860 770 600 722Q330 690 0 612Z" fill="url(#heroPaint)"/>
</svg>

<header>
  <div class="abs display site-logo">Colette Marwick Art</div>
  <nav class="abs main-nav">
    <a style="left:714px;font-weight:700">Home</a>
    <a style="left:814px">About</a>
    <a style="left:914px">My Art</a>
    <a style="left:1020px">Contact</a>
  </nav>
</header>

<div class="abs display hero-title hero-kicker">welcome to</div>
<div class="abs display hero-title hero-name">COLETTE MARWICK ART</div>
<div class="rule" style="left:519px;top:289px;width:162px"></div>

<section>
  <div class="abs about-frame"></div>
  <div class="abs about-photo" role="img" aria-label="Portrait photo of the artist in her studio"></div>
  <div class="abs about-pill"></div>
  <div class="abs about-oval" role="img" aria-label="Detail of a teal and rust abstract painting"></div>
  <h2 class="abs display section-title about-title">ABOUT ME</h2>
  <div class="rule" style="left:608px;top:873px;width:161px"></div>
  <div class="abs about-text">
    <p>Sed ut perspiciatis unde omnis iste natus error sit voluptatem accusantium doloremque laudantium, totam rem aperiam, eaque ipsa quae ab illo inventore veritatis et quasi architecto beatae vitae dicta sunt explicabo.</p>
    <p>&nbsp;Nemo enim ipsam voluptatem quia voluptas sit aspernatur aut odit aut fugit, sed quia consequuntur magni dolores eos qui ratione voluptatem sequi nesciunt. Neque porro quisquam est.</p>
  </div>
  <svg class="abs more-link" viewBox="0 0 31 31"><circle cx="15.5" cy="15.5" r="14.5" fill="none" stroke="#120604" stroke-width="1.5"/><path d="M13.5 10l5 5.5-5 5.5" fill="none" stroke="#120604" stroke-width="1.5"/></svg>
</section>

<section>
  <div class="abs paintings"></div>
  <h2 class="abs display section-title paintings-title">MY PAINTINGS</h2>
  <div class="rule" style="left:519px;top:1423px;width:162px"></div>
  <div class="abs ghost ghost-one">Colette</div>
  <div class="abs ghost ghost-two">Marwick</div>
  <div class="art art-circles" role="img" aria-label="Abstract painting of swirling ochre, blue and orange circles"></div>
  <div class="art art-drips" role="img" aria-label="Abstract painting with blue paint drips running down pale canvas"></div>
  <div class="art art-teal" role="img" aria-label="Abstract painting with a wide teal band between cream stripes"></div>
  <div class="art art-burst" role="img" aria-label="Abstract painting of a dark burst among green and teal strokes"></div>
</section>

<svg class="abs footer-band" viewBox="0 0 1200 483"><path d="M0 107Q600 -110 1200 107V483H0Z" fill="#120604"/></svg>

<footer class="footer">
  <div class="abs display col-title" style="left:109px">Contact Info</div>
  <div class="abs display col-title" style="left:419px">Quick Link</div>
  <div class="abs display col-title" style="left:641px">Get in touch</div>

  <svg class="abs icon" style="top:3103px" viewBox="0 0 22 22"><path d="M11 2a6 6 0 0 0-6 6c0 4.5 6 11 6 11s6-6.5 6-11a6 6 0 0 0-6-6z" fill="#fff"/><circle cx="11" cy="8" r="2.3" fill="#120604"/></svg>
  <div class="abs contact-item" style="top:3096px">Colette Marwick Art<br>Address Comes Here</div>

  <svg class="abs icon" style="top:3169px" viewBox="0 0 22 22"><path d="M3 8c0-3 16-3 16 0v2h-4V8H7v2H3z" fill="#fff"/><rect x="5" y="11" width="12" height="8" rx="2" fill="#fff"/><circle cx="11" cy="15" r="2" fill="#120604"/></svg>
  <div class="abs contact-item" style="top:3165px">+1 555-014-2290</div>

  <svg class="abs icon" style="top:3211px" viewBox="0 0 22 22"><path d="M2 11L20 3l-5 17-4-6z" fill="#fff"/><path d="M11 14l9-11" stroke="#120604" stroke-width="1.2"/></svg>
  <div class="abs contact-item" style="top:3207px">hello@colettemarwick.com</div>

  <div class="abs display follow">Follow:</div>
  <div class="abs social-ring"></div>

  <div class="abs quick-links">Home<br>About<br>My Art<br>Contact</div>

  <div class="field" style="left:641px;top:3103px;width:217px;height:49px">Name</div>
  <div class="field" style="left:873px;top:3103px;width:217px;height:49px">Email</div>
  <div class="field" style="left:641px;top:3170px;width:449px;height:78px">Message</div>
  <div class="abs send">SEND</div>

  <div class="abs footer-rule"></div>
  <div class="abs copyright">2022 Colette Marwick Art. All Rights Reserved.</div>
</footer>

</body>
</html>
```